Debt Collection Website Design! We are the solution for landlords to get paid what they are owed.

We are a 3rd party debt collection company that specializes in Residential and Commercial real estate debt collection. We help landlords recover money from past residents by being fair, friendly and aggressive. We also collect/buy/sell/trade civil judgments won resulting from anything from automobile accidents to evictions to a pet zebra getting stolen. We buy single judgments to large portfolios, we also collect judgments for a nominal fee.

I would like a new, modern, easy to navigate website. A spot that we can post news stories or updated information about our company. I have included our company logo that must be on the top of the page. Feel free to ask any questions that will help get the process going.

Target Market(s)

Landlords, small to large apartment complex. Real estate services and lawyers.

Industry/Entity Type

Real Estate

Number of Pages Required

3 page

Requirements
Must have
• Company logo which has been attached. A page where we can explain the collection process, fees and placement. A page where we can explain judgments, collection vs. selling, placement form. I am open to any font/designs and willing to work with anyone.
Nice to have
• Nice to have a spot on the homepage to place news articles about ourselves and our industry.
Should not have
• I don't want it over crowded. Simple, sleek and easy to navigate is best. No gavels on any of the pages. It cannot look legal, say/show anything that we use legal powers to collect. We are not a law office, we don't practice law, we are 3rd party debt collection agency.

```html
<!DOCTYPE html>
<html lang="en">
<head>
<meta charset="utf-8">
<title>Calden Recovery — Debt Collection</title>
<link href="https://fonts.googleapis.com/css2?family=Bitter:wght@400;500&family=Open+Sans:wght@400;600&family=Raleway:wght@300&display=swap" rel="stylesheet">
<style>
  :root {
    --navy: #15296b;
    --navy-dark: #0f1f55;
    --ink: #2b2b2b;
    --muted: #8a8a8a;
    --page: #e9e9e9;
    --panel: #ffffff;
    --footer: #232323;
    --footer-text: #8d8d8d;
    --social: #3a3a3a;
  }
  * { margin: 0; padding: 0; box-sizing: border-box; }
  html, body { width: 682px; height: 1200px; overflow: hidden; }
  body {
    position: relative;
    background: var(--page) repeating-linear-gradient(90deg, rgba(255,255,255,.25) 0 1px, transparent 1px 3px);
    font-family: "Open Sans", Arial, sans-serif;
    color: var(--ink);
  }
  .site-header {
    position: absolute; top: 0; left: 0; width: 682px; height: 48px;
    background: var(--panel);
    border-top: 2px solid var(--navy);
    border-bottom: 2px solid var(--navy);
  }
  .brand { position: absolute; left: 34px; top: 7px; display: flex; align-items: center; gap: 7px; }
  .brand-mark { width: 26px; height: 26px; background: var(--navy); }
  .brand-name {
    font-family: "Bitter", Georgia, serif; font-weight: 400;
    color: var(--navy); font-size: 15px; line-height: 1.05; letter-spacing: .5px;
  }
  .main-nav { position: absolute; top: 12px; left: 285px; display: flex; }
  .main-nav a {
    display: block; height: 34px; line-height: 34px; padding: 0 15px;
    font-size: 9px; color: #222; text-decoration: none; font-weight: 600;
  }
  .main-nav a.current { background: var(--navy); color: #fff; padding: 0 8px; margin-right: 6px; }

  .hero {
    position: absolute; top: 48px; left: 0; width: 682px; height: 272px;
    background: linear-gradient(160deg, #3d4a5c 0%, #8f8a80 35%, #c9c2b5 55%, #2c3445 80%, #1b2232 100%);
  }
  .hero-caption {
    position: absolute; top: 83px; left: 44px; width: 560px; height: 116px;
    background: rgba(40,40,40,.62); text-align: center; color: #fff;
  }
  .hero-caption h1 { font-family: "Raleway", sans-serif; font-weight: 300; font-size: 35px; margin-top: 17px; }
  .hero-caption p { font-size: 15.5px; margin-top: 6px; }
  .hero-arrow {
    position: absolute; top: 129px; width: 35px; height: 35px; border-radius: 50%;
    background: var(--navy-dark); display: flex; align-items: center; justify-content: center;
  }
  .hero-arrow.prev { left: 16px; } .hero-arrow.next { left: 631px; }

  .panel {
    position: absolute; left: 34px; width: 614px; background: var(--panel);
    box-shadow: 0 14px 14px -10px rgba(0,0,0,.28);
  }
  .panel-title { font-family: "Bitter", Georgia, serif; font-weight: 400; font-size: 20px; color: #222; }
  .body-text { font-size: 7.2px; line-height: 12.5px; color: var(--muted); }
  .btn {
    position: absolute; display: block; background: var(--navy); color: #fff;
    font-size: 9.5px; font-weight: 600; text-align: center; border-radius: 2px; text-decoration: none;
  }
  .photo { position: absolute; }

  .welcome { top: 362px; height: 191px; }
  .welcome .panel-title { position: absolute; left: 194px; top: 12px; }
  .welcome .body-text { position: absolute; left: 196px; top: 49px; width: 405px; }
  .welcome .body-text + .body-text { top: 86px; }
  .welcome .btn { left: 195px; top: 149px; width: 67px; height: 28px; line-height: 28px; }

  .services { top: 585px; height: 304px; }
  .services .panel-title { position: absolute; left: 13px; top: 20px; }
  .service { position: absolute; top: 61px; width: 188px; }
  .service .photo { position: static; width: 188px; height: 100px; }
  .service h3 { font-family: "Bitter", Georgia, serif; font-weight: 500; font-size: 17px; color: var(--navy); margin: 12px 0 8px -1px; }
  .service .btn { position: static; width: 65px; height: 24px; line-height: 24px; margin-top: 14px; margin-left: -1px; }

  .news { top: 927px; height: 164px; }
  .news .panel-title { position: absolute; left: 16px; top: 13px; }
  .news-arrows { position: absolute; left: 572px; top: 21px; display: flex; gap: 6px; }
  .news-item { position: absolute; top: 58px; width: 290px; }
  .news-item .photo { left: 0; top: 0; width: 106px; height: 84px; }
  .news-item .copy { position: absolute; left: 120px; top: 0; width: 170px; }
  .news-item h4 { font-family: "Bitter", Georgia, serif; font-weight: 400; font-size: 12px; line-height: 14.5px; color: #222; }
  .news-item time { display: block; font-size: 7.2px; color: #333; margin: 6px 0 7px; }
  .news-item .more { display: block; font-size: 7.2px; color: var(--navy); margin-top: 9px; text-decoration: none; }

  .site-footer {
    position: absolute; top: 1138px; left: 0; width: 682px; height: 62px; background: var(--footer);
    font-size: 7.2px; color: var(--footer-text);
  }
  .footer-nav { position: absolute; left: 34px; top: 18px; }
  .footer-nav span { margin: 0 4px; }
  .copyright { position: absolute; left: 34px; top: 34px; }
  .social { position: absolute; left: 536px; top: 20px; display: flex; gap: 5px; }
  .social span { width: 18px; height: 18px; background: var(--social); }
</style>
</head>
<body>
  <header class="site-header">
    <div class="brand">
      <span class="brand-mark"></span>
      <span class="brand-name">CALDEN<br>RECOVERY, LLC</span>
    </div>
    <nav class="main-nav">
      <a class="current" href="#">Home</a>
      <a href="#">About us</a>
      <a href="#">Services</a>
      <a href="#">News</a>
      <a href="#">Debt Collection</a>
      <a href="#">Contact us</a>
    </nav>
  </header>

  <section class="hero" role="img" aria-label="Business team working at a table with laptop, papers and coffee">
    <div class="hero-caption">
      <h1>Debt collection</h1>
      <p>Specializes in Residential and Commercial real estate debt collection</p>
    </div>
    <span class="hero-arrow prev"><svg width="10" height="10" viewBox="0 0 10 10"><path d="M6.5 1.5 3 5l3.5 3.5" stroke="#fff" stroke-width="1.6" fill="none"/></svg></span>
    <span class="hero-arrow next"><svg width="10" height="10" viewBox="0 0 10 10"><path d="M3.5 1.5 7 5 3.5 8.5" stroke="#fff" stroke-width="1.6" fill="none"/></svg></span>
  </section>

  <section class="panel welcome">
    <div class="photo" style="left:12px;top:12px;width:160px;height:167px;background:linear-gradient(135deg,#6b6660,#d9d6d0 50%,#4a4744);" role="img" aria-label="Colleagues reviewing documents around a tablet"></div>
    <h2 class="panel-title">Welcome to Calden Recovery</h2>
    <p class="body-text">Neque porro quisquam est, qui dolorem ipsum quia dolor sit amet, consectetur, adipisci velit, sed quia non numquam eius modi tempora incidunt ut labore et dolore magnam aliquam quaerat voluptatem.</p>
    <p class="body-text">At vero eos et accusamus et iusto odio dignissimos ducimus qui blanditiis praesentium voluptatum deleniti atque corrupti quos dolores et quas molestias excepturi sint occaecati cupiditate non provident, similique sunt in culpa qui officia deserunt mollitia animi, id est laborum et dolorum fuga. Et harum quidem rerum facilis est et expedita distinctio. Nam libero tempore,</p>
    <a class="btn" href="#">Read More</a>
  </section>

  <section class="panel services">
    <h2 class="panel-title">Our Service</h2>
    <article class="service" style="left:13px;">
      <div class="photo" style="background:linear-gradient(180deg,#4f7fc4 0%,#2b3d5c 45%,#2a2a2a 70%,#8a6a3a 100%);" role="img" aria-label="Modern house with pool at dusk"></div>
      <h3>Residential</h3>
      <p class="body-text">Nemo enim ipsam voluptatem quia voluptas sit aspernatur aut odit aut fugit, sed quia consequuntur magni dolores eos qui ratione...</p>
      <a class="btn" href="#">Read More</a>
    </article>
    <article class="service" style="left:214px;">
      <div class="photo" style="background:linear-gradient(135deg,#e8eef3 0%,#b7c6d3 40%,#3f5b74 75%,#1e3347 100%);" role="img" aria-label="Glass office tower"></div>
      <h3>Commercial</h3>
      <p class="body-text">Nemo enim ipsam voluptatem quia voluptas sit aspernatur aut odit aut fugit, sed quia consequuntur magni dolores eos qui ratione...</p>
      <a class="btn" href="#">Read More</a>
    </article>
    <article class="service" style="left:412px;">
      <div class="photo" style="background:linear-gradient(135deg,#8fa48a 0%,#c9cfcf 40%,#3a3d42 70%,#1c1e22 100%);" role="img" aria-label="Driver in a car"></div>
      <h3>Automobile</h3>
      <p class="body-text">Nemo enim ipsam voluptatem quia voluptas sit aspernatur aut odit aut fugit, sed quia consequuntur magni dolores eos qui ratione...</p>
      <a class="btn" href="#">Read More</a>
    </article>
  </section>

  <section class="panel news">
    <h2 class="panel-title">Latest News</h2>
    <div class="news-arrows">
      <svg width="10" height="12" viewBox="0 0 10 12"><path d="M7 1.5 2.5 6 7 10.5" stroke="#222" stroke-width="1.6" fill="none"/></svg>
      <svg width="10" height="12" viewBox="0 0 10 12"><path d="M3 1.5 7.5 6 3 10.5" stroke="#222" stroke-width="1.6" fill="none"/></svg>
    </div>
    <article class="news-item" style="left:20px;">
      <div class="photo" style="background:linear-gradient(135deg,#d8dde2,#7d8896 50%,#2e3848);" role="img" aria-label="Two business people reviewing a tablet"></div>
      <div class="copy">
        <h4>Residential and Commercial Real estate</h4>
        <time>24 Feb 2015</time>
        <p class="body-text" style="line-height:9.5px;">Nemo enim ipsam voluptatem quia voluptas sit aspernatur aut odit aut fugit,</p>
        <a class="more" href="#">Read More</a>
      </div>
    </article>
    <article class="news-item" style="left:315px;">
      <div class="photo" style="background:linear-gradient(135deg,#1e1e22,#6b6b70 45%,#e4e4e4);" role="img" aria-label="Business handshake"></div>
      <div class="copy" style="left:118px;">
        <h4>Residential and Commercial Real estate</h4>
        <time>24 Feb 2015</time>
        <p class="body-text" style="line-height:9.5px;">Nemo enim ipsam voluptatem quia voluptas sit aspernatur aut odit aut fugit,</p>
        <a class="more" href="#">Read More</a>
      </div>
    </article>
  </section>

  <footer class="site-footer">
    <nav class="footer-nav">Home<span>/</span>About us<span>/</span>Services<span>/</span>News<span>/</span>Debt Collection<span>/</span>Contact us</nav>
    <p class="copyright">©2015 Calden Recovery. All rights reserved.</p>
    <div class="social" aria-label="Social links">
      <span></span><span></span><span></span><span></span><span></span>
    </div>
  </footer>
</body>
</html>
```